Need 3 posters for in-store display

Hi Marlene,

Hope you are well.
I need 3 posters for display in my restaurant.

Poster 1: To be print in A1 size vertical
Title: YUMBELLA COMBO $19.50
Choose any Pho OR Noodle Salads
Choose Spring Rolls (5 rolls) OR Ricepaper Rolls (2 rolls)
Choose any Cans OR Water

What I like to see:
- These poster will be place near my counter so I want it to grab customer attention.
- You must use photos to show products
- Make it easy to understand and for customer to follow

Poster 2: To be print in A4 size vertical
Title: ADD TO YOUR ORDER
SpringRolls (Crab / vegetarian) $6 / 5 rolls
Extra Meat $2
Extra Noodles $1
Extra Vegs $1.5
Extra Tofu $2
Extra Crackling $3

Poster 3: To be print in A1 size vertical
Title: FIESTO LOOMA PARTY
Catering Menu Options:
- PHO (Beef, Chicken, Vegan) $12.50 per bowl
- NOODLE SALADS (Beef, Chicken, BBQ Pork, Vegan) $12.50 per bowl
- SpringRolls (Crab / vegetarian) $12.50 for 10 rolls
- Ricepaper Rolls (Prawn, Beef, Chicken, BBQ Pork, Tofu) $12.5 / 5 rolls
- Fried Rice (Prawn, Tofu) $50 per tray (serve 5-6)

Terms & Conditions for All Catering Orders:
1) Minimum orders $200 (Pick-Up from shop Only)
2) All orders must be paid upfront
3) Requires $300 bond for Soup Tank
4) Please give us 48hours notice

• For the YUMBELLA COMBO
• it would be nice to have an image of the battle of water to visually complete the meal deal
• please see attachment of the Crestvale Peak Water

```html
<!DOCTYPE html>
<html lang="en">
<head>
<meta charset="utf-8">
<title>Add To Your Order</title>
<link rel="stylesheet" href="https://fonts.googleapis.com/css2?family=Oswald:wght@700&family=Open+Sans:wght@400;600;700&display=swap">
<style>
  :root {
    --ink: #000000;
    --paper: #ffffff;
    --gold-light: #f6d98a;
    --gold: #d9ae4a;
    --gold-deep: #b8862a;
    --lime: #a6c93a;
    --slate: #2a3038;
    --footer-text: #3b3222;
  }
  * { margin: 0; padding: 0; box-sizing: border-box; }
  html, body { width: 872px; height: 1200px; overflow: hidden; background: var(--ink); }
  .poster {
    position: relative;
    width: 872px;
    height: 1200px;
    background: var(--ink);
    font-family: "Open Sans", sans-serif;
    color: var(--paper);
  }
  .title {
    position: absolute;
    left: 0; right: 0; top: 48px;
    text-align: center;
    font-family: "Oswald", sans-serif;
    font-weight: 700;
    font-size: 78px;
    line-height: 1;
    letter-spacing: 3px;
    background: linear-gradient(180deg, var(--gold-light) 0%, var(--gold) 45%, var(--gold-deep) 100%);
    -webkit-background-clip: text;
    background-clip: text;
    color: transparent;
  }
  .feature-box {
    position: absolute;
    left: 90px; top: 134px;
    width: 695px; height: 48px;
    border: 1.5px solid var(--paper);
    display: flex; align-items: center; justify-content: center;
    font-weight: 700;
    font-size: 22px;
    letter-spacing: 0.3px;
  }
  .extra-label {
    position: absolute;
    left: 144px; top: 253px;
    width: 70px; height: 290px;
  }
  .extra-label span {
    position: absolute;
    left: 50%; top: 50%;
    transform: translate(-50%, -50%) rotate(-90deg);
    font-family: "Open Sans", sans-serif;
    font-weight: 700;
    font-size: 84px;
    line-height: 1;
    letter-spacing: -2px;
    background: linear-gradient(90deg, var(--gold-deep), var(--gold-light) 55%, var(--gold));
    -webkit-background-clip: text;
    background-clip: text;
    color: transparent;
    white-space: nowrap;
  }
  .extras {
    position: absolute;
    left: 226px; top: 250px;
    list-style: none;
  }
  .extras li {
    display: grid;
    grid-template-columns: 397px auto;
    align-items: baseline;
    height: 60px;
    font-size: 52px;
    line-height: 60px;
  }
  .item { display: flex; align-items: baseline; }
  .item-name { letter-spacing: -0.5px; }
  .leader {
    flex: 1;
    height: 6px;
    margin: 0 2px 0 4px;
    background-image: radial-gradient(circle, var(--lime) 1.8px, transparent 2.2px);
    background-size: 11px 6px;
    background-repeat: repeat-x;
  }
  .price { color: var(--lime); font-weight: 700; }
  .photo {
    position: absolute;
    left: 0; top: 572px;
    width: 872px; height: 548px;
  }
  .footer {
    position: absolute;
    left: 0; bottom: 0;
    width: 872px; height: 80px;
    background: linear-gradient(90deg, var(--gold) 0%, var(--gold-light) 55%, var(--gold) 100%);
    color: var(--footer-text);
    font-size: 22px;
    display: flex; align-items: center; justify-content: space-between;
    padding: 0 44px 0 43px;
  }
  .web { display: flex; align-items: center; gap: 12px; }
</style>
</head>
<body>
  <main class="poster">
    <h1 class="title">ADD TO YOUR ORDER</h1>
    <p class="feature-box">SPRINGROLLS (CRAB / VEGETARIAN) $6 / 5 ROLLS</p>

    <div class="extra-label"><span>EXTRA</span></div>
    <ul class="extras">
      <li><span class="item"><span class="item-name">MEAT</span><span class="leader"></span></span><span class="price">$2</span></li>
      <li><span class="item"><span class="item-name">NOODLES</span><span class="leader"></span></span><span class="price">$1</span></li>
      <li><span class="item"><span class="item-name">VEGS</span><span class="leader"></span></span><span class="price">$1.5</span></li>
      <li><span class="item"><span class="item-name">TOFU</span><span class="leader"></span></span><span class="price">$2</span></li>
      <li><span class="item"><span class="item-name">CRACKLING</span><span class="leader"></span></span><span class="price">$3</span></li>
    </ul>

    <svg class="photo" role="img" aria-label="Photo of two golden fried spring rolls on a white plate with a dipping sauce and fresh basil" viewBox="0 0 872 548">
      <defs>
        <linearGradient id="tableFade" x1="0" y1="0" x2="0" y2="1">
          <stop offset="0" stop-color="#000000"/>
          <stop offset="0.22" stop-color="#1d232b"/>
          <stop offset="1" stop-color="#262c34"/>
        </linearGradient>
        <radialGradient id="plateGlow" cx="0.55" cy="0.6" r="0.55">
          <stop offset="0" stop-color="#c98a45" stop-opacity="0.85"/>
          <stop offset="0.45" stop-color="#8a7766" stop-opacity="0.55"/>
          <stop offset="1" stop-color="#262c34" stop-opacity="0"/>
        </radialGradient>
      </defs>
      <rect width="872" height="548" fill="url(#tableFade)"/>
      <rect width="872" height="548" fill="url(#plateGlow)"/>
    </svg>

    <footer class="footer">
      <span class="phone">Call Us:0400 555 218</span>
      <span class="web">
        <svg width="30" height="30" viewBox="0 0 30 30" aria-hidden="true">
          <g fill="none" stroke="#2a2418" stroke-width="1.6">
            <circle cx="15" cy="15" r="13"/>
            <circle cx="15" cy="15" r="9"/>
            <ellipse cx="15" cy="15" rx="4" ry="9"/>
            <line x1="6" y1="15" x2="24" y2="15"/>
            <line x1="7.5" y1="10.5" x2="22.5" y2="10.5"/>
            <line x1="7.5" y1="19.5" x2="22.5" y2="19.5"/>
          </g>
        </svg>
        www.fiestolooma.com
      </span>
    </footer>
  </main>
</body>
</html>
```